Business card, Invoice and printable service brochure

I need a 5.5x8.5 invoice, business card and printable service template for reception desk designed for my Rug repair, restoration and cleaning business.

I have included a picture for reference

www.velborenrug.example

Columns i need in my invoice:
Type of rug, Size, Background Color, Repair needs, Notes, Price and rug cleaning disclaimer.

Target Market(s)

Higher segment clients

Industry/Entity Type

Rug Repair, Restoration and cleaning,

Requirements
Must have
• Services hast to be listed on the invoice as well as service brochure.

```html
<!DOCTYPE html>
<html lang="en">
<head>
<meta charset="utf-8">
<title>Velboren Rug – Service Brochure</title>
<link rel="stylesheet" href="https://fonts.googleapis.com/css2?family=Open+Sans:wght@300;400;600;700;800&display=swap">
<style>
  :root {
    --backdrop: #4b4b4d;
    --paper-dark: #34332f;
    --paper-deep: #252421;
    --paper-light: #f4f3f1;
    --gold: #c79a2a;
    --gold-deep: #8f6a14;
    --accent-yellow: #f1c232;
    --logo-beige: #cbb68c;
    --text-white: #f3f1ec;
    --text-soft: #d8d5cf;
    --bar-gray: #8e979b;
  }
  * { margin: 0; padding: 0; box-sizing: border-box; }
  html, body { width: 1199px; height: 1200px; overflow: hidden; }
  body {
    background: var(--backdrop);
    font-family: "Open Sans", Arial, sans-serif;
    color: var(--text-white);
    position: relative;
  }
  .brochure-sheet {
    position: absolute;
    left: 40px; top: 30px;
    width: 1120px; height: 1140px;
    display: grid;
    grid-template-columns: 560px 560px;
    grid-template-rows: 570px 570px;
    box-shadow: 0 20px 40px rgba(0,0,0,.35);
  }
  .panel {
    position: relative;
    overflow: hidden;
    background: linear-gradient(160deg, var(--paper-dark), var(--paper-deep));
  }
  .panel + .panel { border-left: 1px solid rgba(0,0,0,.25); }
  .panel-intro, .panel-story { border-right: 1px solid rgba(255,255,255,.06); }
  .panel-story, .panel-services-more { border-top: 1px solid rgba(255,255,255,.06); }

  .placeholder { position: absolute; }
  .photo-circle {
    position: absolute;
    border-radius: 50%;
    box-shadow: 0 4px 10px rgba(0,0,0,.35);
  }
  .loom-sketch {
    background: linear-gradient(180deg, rgba(255,255,255,.08), rgba(255,255,255,.03));
  }
  .gold-ornament {
    background: linear-gradient(90deg, var(--gold-deep), var(--gold) 40%, var(--gold-deep) 70%, var(--gold));
  }

  /* Intro panel */
  .brand-name {
    position: absolute; left: 40px; top: 62px;
    font-weight: 300; font-size: 52px; letter-spacing: 5px;
    color: var(--logo-beige);
  }
  .brand-tagline {
    position: absolute; left: 44px; top: 132px;
    font-size: 12px; letter-spacing: 5px; color: var(--logo-beige);
  }
  .experience-line {
    position: absolute; left: 210px; top: 340px; width: 320px;
    font-weight: 700; font-size: 24px; line-height: 1.15;
  }
  .feature-title {
    position: absolute; left: 290px; top: 452px;
    font-weight: 700; font-size: 25px;
  }
  .feature-sub {
    position: absolute; left: 292px; top: 486px;
    font-size: 15px; color: var(--text-soft);
  }

  /* Story panel */
  .light-band {
    position: absolute; left: 0; top: 0; width: 560px; height: 200px;
    background: var(--paper-light);
  }
  .story-heading {
    position: absolute; font-weight: 800; font-size: 14px; line-height: 1.1;
    color: var(--gold);
  }
  .story-copy {
    position: absolute; font-size: 7.5px; line-height: 1.45;
  }
  .story-copy.on-light { color: #4a4844; }
  .story-copy.on-dark { color: var(--text-soft); }
  .story-copy p + p { margin-top: 6px; }

  /* Service panels */
  .service-tag {
    position: absolute; left: 48px; top: 36px;
    display: flex; align-items: center; gap: 14px;
  }
  .service-tag .bar { width: 6px; height: 46px; background: var(--bar-gray); }
  .service-tag h2 {
    font-weight: 800; font-size: 40px; color: var(--accent-yellow); letter-spacing: 1px;
  }
  .service-item {
    position: absolute; width: 380px;
  }
  .service-item h3 {
    font-weight: 700; font-size: 22px; line-height: 1.1; margin-bottom: 6px;
  }
  .service-item p {
    font-size: 10.5px; line-height: 1.4; color: var(--text-soft);
  }
</style>
</head>
<body>
<main class="brochure-sheet">

  <section class="panel panel-intro">
    <div class="placeholder loom-sketch" style="left:0;top:330px;width:270px;height:240px" role="img" aria-label="Line sketch of a rug loom"></div>
    <div class="brand-name">VELBOREN RUG</div>
    <div class="brand-tagline">REPAIR | RESTORATION | CLEANING</div>
    <div class="photo-circle" style="left:40px;top:180px;width:130px;height:130px;background:radial-gradient(circle at 40% 40%,#b58b6a,#5c4434)" role="img" aria-label="Photo of a craftsman reweaving a rug by hand"></div>
    <div class="photo-circle" style="left:180px;top:180px;width:130px;height:130px;background:radial-gradient(circle at 50% 40%,#9b8a8e,#4e5a48)" role="img" aria-label="Photo of a rug drying outdoors among plants"></div>
    <div class="photo-circle" style="left:320px;top:180px;width:130px;height:130px;background:radial-gradient(circle at 50% 50%,#c27a4c,#6b3b24)" role="img" aria-label="Photo of a rug being deep cleaned with a wand"></div>
    <div class="experience-line">30+ years of EXPERIENCE in rug restoration field</div>
    <div class="feature-title">Oriental Rug Repair</div>
    <div class="feature-sub">Authenticity and perfection.</div>
  </section>

  <section class="panel panel-services">
    <div class="placeholder gold-ornament" style="left:490px;top:0;width:52px;height:470px" role="img" aria-label="Gold illustrated rug border, vertical"></div>
    <div class="placeholder gold-ornament" style="left:12px;top:330px;width:60px;height:200px" role="img" aria-label="Gold illustrated rug corner"></div>
    <div class="service-tag"><span class="bar"></span><h2>SERVICE</h2></div>
    <article class="service-item" style="left:90px;top:108px">
      <h3>Antique Rug Repair</h3>
      <p>Our Antique Rug Repair can help you improve your customer retention rate by giving you access to our team of expert weavers who are trained in various kinds of repairs, such as re-surging area rug, binding area rug, leather rug support, re-fringing area rug as well as discoloration on the pile. We also offer free estimates for all types of projects so that you know exactly what it will cost before getting started!</p>
    </article>
    <article class="service-item" style="left:90px;top:262px">
      <h3>Antique Rug Cleaning</h3>
      <p>Our Antique Rug Repair can help you improve your customer retention rate by giving you access to our team of expert weavers who are trained in various kinds of repairs, such as re-surging area rug, binding area rug, leather rug support, re-fringing area rug as well as discoloration on the pile. We also offer free estimates for all types of projects so that you know exactly what it will cost before getting started!</p>
    </article>
    <article class="service-item" style="left:90px;top:410px">
      <h3>Exemplary Customer Service</h3>
      <p>Our Antique Rug Repair can help you improve your customer retention rate by giving you access to our team of expert weavers who are trained in various kinds of repairs, such as re-surging area rug, binding area rug, leather rug support, re-fringing area rug as well as discoloration on the pile. We also offer free estimates for all types of projects so that you know exactly what it will cost before getting started!</p>
    </article>
  </section>

  <section class="panel panel-story">
    <div class="placeholder loom-sketch" style="left:0;top:200px;width:200px;height:200px" role="img" aria-label="Line sketch of a rug loom, continued"></div>
    <div class="light-band"></div>
    <div class="story-heading" style="left:36px;top:70px;width:240px">THERE IS NOTHING MORE PRECIOUS THAN THE ORIGINAL.</div>
    <div class="story-copy on-light" style="left:36px;top:106px;width:240px">
      <p>We value authenticity and built our name on restoring rugs by hand, bringing back the life and story of pieces that families treasure. Each repair respects the original weave, dyes and craftsmanship, so your rug keeps its character and value for the next generation to enjoy.</p>
    </div>
    <div class="photo-circle" style="left:300px;top:20px;width:210px;height:210px;background:radial-gradient(circle at 40% 50%,#8a5a36,#3e3f42)" role="img" aria-label="Photo of a wooden cabinet and chair on a red rug"></div>
    <div class="photo-circle" style="left:50px;top:240px;width:200px;height:200px;background:radial-gradient(circle at 50% 60%,#8a6a44,#3f4540)" role="img" aria-label="Photo of a living room with plants and a round rug"></div>
    <div class="story-heading" style="left:290px;top:250px;width:240px">WE CARE AND RESPECT THE RUGS WE WORK ON.</div>
    <div class="story-copy on-dark" style="left:290px;top:286px;width:240px">
      <p>With over 30 years of expertise in restoring and cleaning fine rugs, we feel we have a duty to bring each rug to its former glory. Our workshop handles hand-knotted, antique and oriental pieces with the same careful attention, from gentle washing to detailed reweaving.</p>
      <p>We know the work and passion that went into every handmade rug. Our team treats your piece as an heirloom and is proud to help keep it beautiful for many years to come.</p>
    </div>
    <div class="placeholder gold-ornament" style="left:40px;top:470px;width:500px;height:100px" role="img" aria-label="Gold illustrated rug border with floral pattern"></div>
  </section>

  <section class="panel panel-services-more">
    <article class="service-item" style="left:90px;top:30px">
      <h3>Oriental Rug Restoration</h3>
      <p>Our Antique Rug Repair can help you improve your customer retention rate by giving you access to our team of expert weavers who are trained in various kinds of repairs, such as re-surging area rug, binding area rug, leather rug support, re-fringing area rug as well as discoloration on the pile. We also offer free estimates for all types of projects so that you know exactly what it will cost before getting started!</p>
    </article>
    <article class="service-item" style="left:90px;top:190px">
      <h3>Staircase Rug Installation</h3>
      <p>Our Antique Rug Repair can help you improve your customer retention rate by giving you access to our team of expert weavers who are trained in various kinds of repairs, such as re-surging area rug, binding area rug, leather rug support, re-fringing area rug as well as discoloration on the pile. We also offer free estimates for all types of projects so that you know exactly what it will cost before getting started!</p>
    </article>
    <article class="service-item" style="left:90px;top:360px">
      <h3>Sun fade or Color Correction</h3>
      <p>Our Antique Rug Repair can help you improve your customer retention rate by giving you access to our team of expert weavers who are trained in various kinds of repairs, such as re-surging area rug, binding area rug, leather rug support, re-fringing area rug as well as discoloration on the pile. We also offer free estimates for all types of projects so that you know exactly what it will cost before getting started!</p>
    </article>
    <div class="placeholder gold-ornament" style="left:0;top:550px;width:420px;height:20px" role="img" aria-label="Gold illustrated rug border edge"></div>
  </section>

</main>
</body>
</html>
```